Design a web site for my business - Brightline Coatings Co.

We are a family business that handles design, fabrication and installation of powder coated aluminum, stainless steel and glass products. Including handrails, privacy slat screens, electric gates and pool fencing. We are based in the Whitsundays in North Queensland and service an area from Airlie Beach to Townsville.

Target Market(s)

Domestic and commercial

Industry/Entity Type

fabrication - manufacturing

Coding

Coded - Design and coding required

Number of Pages Required

5+ page

Colors
0054AA
0677BA
7BADD7
CADEEF
E8F1F8

Requirements
Must have
• photo galleries, contact page, one page for privacy screens, balustrades, glass fencing, stainless steel handrail, powder coated aluminium handrails and pool fencing

```html
<!DOCTYPE html>
<html lang="en">
<head>
<meta charset="utf-8">
<title>Brightline Coatings Co — Custom Fabrication</title>
<link href="https://fonts.googleapis.com/css2?family=Exo+2:wght@700;800&family=Poppins:wght@400;500;600&display=swap" rel="stylesheet">
<style>
:root{
  --blue:#0054AA;
  --blue-mid:#0677BA;
  --blue-soft:#7BADD7;
  --blue-pale:#CADEEF;
  --blue-mist:#E8F1F8;
  --navy:#13253a;
  --ink:#1b2430;
  --grey-bg:#eef1f5;
  --text:#4a5360;
  --white:#fff;
}
*{box-sizing:border-box;margin:0;padding:0}
html,body{width:1200px;height:4955px;overflow:hidden}
body{font-family:"Poppins",sans-serif;color:var(--text);background:var(--white);position:relative}
.abs{position:absolute}
h1,h2,h3,h4,.display{font-family:"Exo 2",sans-serif;font-weight:800;color:var(--ink);text-transform:uppercase;letter-spacing:.5px}
.btn{position:absolute;display:flex;align-items:center;justify-content:center;background:var(--blue-mid);color:#fff;font-size:10px;font-weight:600;text-transform:uppercase;letter-spacing:.3px}
.btn-outline{background:transparent;border:1.5px solid #fff}
.brand{font-family:"Exo 2",sans-serif;font-weight:800;text-transform:uppercase;display:flex;align-items:center;gap:8px}
.brand .mark{width:12px;height:12px;background:currentColor;display:inline-block}

/* hero */
.hero{left:0;top:0;width:1200px;height:706px}
.hero-photo{position:absolute;inset:0;background:linear-gradient(180deg,#3d566e 0%,#2a4862 40%,#1f3d57 70%,#243a4c 100%)}
.hero .brand{left:125px;top:78px;color:#fff;font-size:13px}
.nav{left:596px;top:44px;display:flex;gap:17px;color:#fff;font-size:11px}
.hero h1{left:137px;top:440px;color:#fff;font-size:37px;line-height:41px}
.hero-lead{left:760px;top:477px;width:300px;color:#fff;font-size:10px;line-height:15px}
.dots{left:137px;top:655px;display:flex;gap:6px}
.dots i{width:5px;height:5px;border-radius:50%;background:#8aa0b4}
.dots i:first-child{background:var(--blue-soft)}

/* about */
.eyebrow{color:var(--blue);font-size:13px;font-weight:600;display:flex;align-items:center;gap:10px;text-transform:uppercase}
.eyebrow::before{content:"";width:40px;height:1.5px;background:var(--blue-mid)}
.about-photo{left:527px;top:946px;width:567px;height:375px;background:linear-gradient(160deg,#5a7a8e,#3d5f76 50%,#6c7f88)}
.tile{width:148px;height:183px;padding:34px 28px;color:#fff}
.tile h4{color:#fff;font-size:14px;line-height:16px;margin-bottom:10px}
.tile p{font-size:9px;line-height:14px}
.tile svg{margin-top:12px}
.about-text{left:125px;top:1016px;width:335px}
.about-text h3{font-size:18px;margin-bottom:16px}
.about-text p{font-size:9.5px;line-height:15.5px;margin-bottom:10px}

/* services */
.services-photo{left:0;top:1435px;width:1200px;height:550px;background:linear-gradient(180deg,#3f5a3f 0%,#6a7560 40%,#9fa7a1 65%,#eef1f5 92%)}
.services-head{left:613px;top:1435px;width:587px;height:138px;background:#fff;justify-content:center;font-size:33px;color:var(--ink)}
.service{width:300px}
.service .ico{width:64px;height:64px;background:var(--blue-mid);display:flex;align-items:center;justify-content:center;margin-bottom:24px;border:3px solid rgba(255,255,255,.6)}
.service h3{font-size:18px;margin-bottom:12px}
.service p{font-size:10px;line-height:15px;color:var(--ink)}
.process-bg{left:0;top:1985px;width:1200px;height:692px;background:var(--grey-bg)}
.process-title{left:0;top:2030px;width:1200px;text-align:center;font-size:30px}
.process-photo{left:148px;top:2152px;width:429px;height:419px;background:linear-gradient(180deg,#a8b6c2 0%,#5a4638 40%,#3a2e28 60%,#4f6a45 100%);box-shadow:0 10px 30px rgba(0,0,0,.15)}
.steps{left:656px;top:2212px;width:400px}
.step{border-bottom:1px solid #d5dbe2;padding:12px 0 16px}
.step:last-child{border:none}
.step h4{font-size:18px}
.step.active h4{color:var(--blue-mid)}
.step p{font-size:9.5px;line-height:15px;margin-top:10px;width:360px}

/* portfolio */
.portfolio h2{left:158px;top:2782px;font-size:32px;line-height:35px}
.card{top:2888px;width:425px;height:383px;background:linear-gradient(180deg,#2b4a66 0%,#22384f 55%,#1c2a38 100%);overflow:hidden}
.card .inner{position:absolute;left:48px;top:258px;width:320px;color:#fff}
.card h3{color:#fff;font-size:18px;margin-bottom:12px}
.card p{font-size:9.5px;line-height:15px}
.card-arrow{width:50px;height:48px;background:var(--blue-mid);display:flex;align-items:center;justify-content:center;top:3250px}
.slider-bars{left:552px;top:3352px;display:flex;gap:8px}
.slider-bars i{width:50px;height:3px;background:var(--ink)}
.slider-bars i.on{background:var(--blue-mid)}

/* region */
.divider{left:0;top:3423px;width:1200px;height:1px;background:#e3e7ec}
.region h2{left:183px;top:3562px;font-size:32px;line-height:35px}
.region-text{left:183px;top:3690px;width:350px}
.region-text p{font-size:9.5px;line-height:15.5px;margin-bottom:12px}
.map{left:611px;top:3477px;width:495px;height:436px;background:radial-gradient(ellipse at 60% 55%,#dbe8f4 0%,#eaf2f9 55%,#fff 90%)}

/* contact */
.form-box{left:171px;top:3965px;width:437px;height:477px;background:var(--blue);padding:45px 42px}
.field{background:#fff;height:45px;margin-bottom:10px;font-size:10px;color:var(--ink);padding:15px 26px}
.field.msg{height:111px}
.form-submit{height:45px;background:var(--navy);color:#fff;font-size:10px;font-weight:600;text-transform:uppercase;display:flex;align-items:center;justify-content:center}
.cta .brand{left:672px;top:4090px;color:var(--ink);font-size:18px}
.cta h2{left:698px;top:4178px;font-size:31px;line-height:35px}
.cta p{left:698px;top:4265px;width:340px;font-size:9.5px;line-height:15px}

/* footer */
.footer{left:0;top:4552px;width:1200px;height:403px;background:var(--navy);color:#fff}
.footer .brand{position:absolute;left:125px;top:208px;font-size:15px;color:#fff}
.col{position:absolute;top:107px}
.col h4{color:#fff;font-size:15px;margin-bottom:22px}
.col li{list-style:none;font-size:9px;line-height:19px;color:#cdd5de}
.col .lbl{font-size:8px;font-weight:600;color:#fff;margin-top:6px}
.col .val{font-size:9px;line-height:13px;color:#cdd5de}
.news-input{width:210px;height:28px;background:#2a3b50;font-size:8.5px;color:#cdd5de;padding:8px 16px;margin:14px 0 10px}
.news-btn{width:210px;height:28px;background:var(--blue-mid);display:flex;align-items:center;justify-content:center;font-size:9px;font-weight:600;text-transform:uppercase;position:relative}
.news-btn svg{position:absolute;right:10px}
.copyright{position:absolute;left:0;top:370px;width:1200px;text-align:center;font-size:8.5px;color:#cdd5de}
</style>
</head>
<body>

<section class="hero abs">
  <div class="hero-photo" role="img" aria-label="Waterfront boardwalk with powder-coated balustrade along a rocky bay at dusk"></div>
  <div class="brand abs"><span class="mark"></span>Brightline Coatings Co</div>
  <nav class="nav abs"><span>Home</span><span>About Us</span><span>Services</span><span>Gallery</span><span>Contact</span></nav>
  <a class="btn" style="left:904px;top:33px;width:172px;height:38px">Request a free quote</a>
  <h1 class="abs">Expert custom<br>fabrication for the<br>Whitsundays &amp; beyond.</h1>
  <p class="hero-lead abs">Premium powder-coated aluminum, stainless steel, and glass solutions for domestic and commercial projects. Serving Airlie Beach to Townsville.</p>
  <div class="dots abs"><i></i><i></i><i></i></div>
  <a class="btn" style="left:760px;top:638px;width:140px;height:38px">View our work</a>
  <a class="btn btn-outline" style="left:917px;top:638px;width:145px;height:38px">Request a quote</a>
</section>

<section class="about">
  <div class="eyebrow abs" style="left:125px;top:810px">What we do</div>
  <h2 class="abs" style="left:398px;top:784px;font-size:31px;line-height:35px">Quality craftsmanship,<br>family values.</h2>
  <div class="about-photo abs" role="img" aria-label="Coastal boardwalk with railings beside flowering trees and the sea"></div>
  <div class="tile abs" style="left:733px;top:871px;background:var(--blue-mid)">
    <h4>Our<br>mission</h4>
    <p>It is a long fact that a reader will be distracted by the</p>
    <svg width="18" height="12" viewBox="0 0 18 12"><path d="M0 6h16M11 1l5 5-5 5" stroke="#fff" stroke-width="1.5" fill="none"/></svg>
  </div>
  <div class="tile abs" style="left:898px;top:871px;background:#5aa3d6">
    <h4>Our<br>vision</h4>
    <p>It is a long fact that a reader will be distracted by the</p>
    <svg width="18" height="12" viewBox="0 0 18 12"><path d="M0 6h16M11 1l5 5-5 5" stroke="#fff" stroke-width="1.5" fill="none"/></svg>
  </div>
  <div class="about-text abs">
    <h3>About Brightline</h3>
    <p>As a locally owned family business, we take pride in delivering custom fabrication solutions that combine durability, functionality, and modern design. Every project is carefully designed, manufactured, and installed by our experienced team using premium aluminium, stainless steel, and glass materials.</p>
    <p>Whether you're upgrading your home or completing a commercial development, we're committed to delivering outstanding workmanship and reliable service from consultation through installation.</p>
  </div>
  <a class="btn" style="left:125px;top:1210px;width:173px;height:38px">Learn more about us</a>
</section>

<section class="services">
  <div class="services-photo abs" role="img" aria-label="Timber deck with stainless steel wire balustrade among tropical trees"></div>
  <div class="services-head abs brand"><span class="mark" style="width:16px;height:16px"></span>Our services</div>
  <div class="service abs" style="left:125px;top:1792px">
    <div class="ico"><svg width="30" height="26" viewBox="0 0 30 26" fill="none" stroke="#fff" stroke-width="1.5"><rect x="2" y="2" width="26" height="22"/><path d="M7 2v22M12 2v22M17 2v22M22 2v22"/></svg></div>
    <h3>Privacy slat screens</h3>
    <p>Modern powder coated aluminium privacy screens that provide security, airflow and contemporary style.</p>
  </div>
  <div class="service abs" style="left:513px;top:1792px">
    <div class="ico"><svg width="30" height="26" viewBox="0 0 30 26" fill="none" stroke="#fff" stroke-width="1.5"><path d="M2 24h26M4 6h22M6 6v18M12 6v18M18 6v18M24 6v18"/></svg></div>
    <h3>Balustrades</h3>
    <p>Custom aluminium, stainless steel and glass balustrades designed to enhance safety without compromising aesthetics.</p>
  </div>
  <div class="service abs" style="left:904px;top:1792px">
    <div class="ico"><svg width="30" height="26" viewBox="0 0 30 26" fill="none" stroke="#fff" stroke-width="1.5"><rect x="2" y="4" width="26" height="18"/><path d="M2 13h26M8 4v18M15 4v18M22 4v18"/></svg></div>
    <h3>Glass fencing</h3>
    <p>Frameless and semi-frameless glass fencing that creates a clean, open look for pools, patios and outdoor entertaining areas.</p>
  </div>
</section>

<section class="process">
  <div class="process-bg abs"></div>
  <h2 class="process-title abs">Simple process. Exceptional results.</h2>
  <div class="process-photo abs" role="img" aria-label="Elevated timber home with glass and stainless steel balustrade"></div>
  <div class="steps abs">
    <div class="step"><h4>01. Consultation</h4></div>
    <div class="step active"><h4>02. Design &amp; Quote</h4><p>After understanding your requirements, we prepare a customised design and provide a clear, transparent quotation. Every solution is tailored to suit your style, budget and project specifications.</p></div>
    <div class="step"><h4>03. Fabrication</h4></div>
    <div class="step"><h4>04. Installation</h4></div>
  </div>
</section>

<section class="portfolio">
  <h2 class="abs">Brightline<br>portfolio projects</h2>
  <a class="btn" style="left:900px;top:2800px;width:141px;height:37px">View our work</a>
  <div class="card abs" style="left:125px" role="img" aria-label="Frameless glass pool fence among tropical plants">
    <div class="inner"><h3>Some goes project here</h3><p>It is a long established fact that a reader will be distracted by the readable content of a page when looking at its layout.</p></div>
  </div>
  <div class="card abs" style="left:567px" role="img" aria-label="Powder-coated aluminium slat privacy screen">
    <div class="inner"><h3>Some goes project here</h3><p>It is a long established fact that a reader will be distracted by the readable content of a page when looking at its layout.</p></div>
  </div>
  <div class="card abs" style="left:1010px" role="img" aria-label="Stainless steel wire balustrade on coastal steps">
    <div class="inner"><h3>Some goes project here</h3><p>It is a long established fact that a reader will be distracted by the readable content of a page when looking at its layout.</p></div>
  </div>
  <div class="card-arrow abs" style="left:462px"><svg width="20" height="14" viewBox="0 0 20 14"><path d="M1 7h17M12 1l6 6-6 6" stroke="#fff" stroke-width="1.5" fill="none"/></svg></div>
  <div class="card-arrow abs" style="left:902px"><svg width="20" height="14" viewBox="0 0 20 14"><path d="M1 7h17M12 1l6 6-6 6" stroke="#fff" stroke-width="1.5" fill="none"/></svg></div>
  <div class="slider-bars abs"><i></i><i class="on"></i><i></i></div>
</section>

<section class="region">
  <div class="divider abs"></div>
  <h2 class="abs">Serving the<br>Whitsundays &amp;<br>beyond</h2>
  <div class="region-text abs">
    <p>Based in the beautiful Whitsundays region, we proudly service a broad area of North Queensland from the pristine beaches of Airlie Beach to the vibrant city of Townsville and everywhere in between.</p>
    <p>Whether you're on Hamilton Island, a coastal property in Bowen, or a rural home in Proserpine our team is ready to bring your project to life with the same dedication and quality we're known for.</p>
  </div>
  <div class="map abs" role="img" aria-label="Map of North Queensland service area from Townsville to Gladstone, with Airlie Beach, Bowen and Mackay marked"></div>
</section>

<section class="contact">
  <form class="form-box abs">
    <div class="field">First Name</div>
    <div class="field">Last Name</div>
    <div class="field">Email Address</div>
    <div class="field">Phone Number</div>
    <div class="field msg">Message</div>
    <div class="form-submit">Request a quote</div>
  </form>
  <div class="cta">
    <div class="brand abs"><span class="mark"></span>Brightline Coatings Co</div>
    <h2 class="abs">Ready to start<br>your project?</h2>
    <p class="abs">Whether you're planning a new build, renovation, or commercial project, we're here to provide custom fabrication solutions designed to last.</p>
    <a class="btn" style="left:698px;top:4318px;width:157px;height:38px">Contact us today</a>
  </div>
</section>

<footer class="footer abs">
  <div class="brand"><span class="mark"></span>Brightline Coatings Co</div>
  <div class="col" style="left:357px"><h4>Quick links</h4><ul><li>Home</li><li>About Us</li><li>Services</li><li>Projects</li><li>Our Process</li><li>Contact</li></ul></div>
  <div class="col" style="left:518px"><h4>Help</h4><ul><li>Help center</li><li>FAQs</li><li>Privacy policy</li><li>Cookie policy</li><li>Terms of use</li><li>Cookie settings</li></ul></div>
  <div class="col" style="left:658px"><h4>Contact us</h4>
    <div class="lbl">WEBSITE:</div><div class="val">12 Harbour View Rd, Cannonvale,<br>QLD, Australia</div>
    <div class="lbl">PHONE:</div><div class="val">+61 400 123 456</div>
    <div class="lbl">MAIL US:</div><div class="val">hello@brightlinecoatings.com</div>
  </div>
  <div class="col" style="left:858px"><h4>Newsletter</h4>
    <div class="val" style="color:#fff">Subscribe our mailing list</div>
    <div class="news-input">Email...</div>
    <div class="news-btn">Submit<svg width="12" height="12" viewBox="0 0 12 12"><path d="M1 6l10-5-4 10-1.5-3.5z" fill="#fff"/></svg></div>
  </div>
  <div class="copyright">© 2026 Brightline Coatings Co | All rights reserved</div>
</footer>

</body>
</html>
```